'Velunor' Nutritional supplements label design (UPDATED)

- 'Velunor' is a upscale health supplements brand
-The company will be packing the products in plastic bottles like other supplements
-Try to use a distinct design which is recognizable from distance
-Brand Logo is attached

-UPDATE- 2-

Label Dimensions and Design:

Hi Everyone,

Sorry for the late response caused by some very busy schedule.

Anyhow, here are the dimensions of the label (Self Adhesive) that we need:

Length of Label : 18cm
Height of Label : 6.5 cm

Product Names:

-Metabolism Formula
-Complete Multivitamins and Minerals (For Men, Women and Kids)
-Healthy Bones
-Skin Support
-Omega-3 oil for Healthy Heart

As for the ingredients just use Lorem Ipsum for now.

Many thanks to all of you in advance.

Target Market(s)

Middle Income families

Industry/Entity Type

Plastic

Requirements
Must have
• -Quality
-Effective
-Unique

```html
<!DOCTYPE html>
<html lang="en">
<head>
<meta charset="utf-8">
<title>Velunor Multi-Vitamin Formula Label</title>
<link rel="stylesheet" href="https://fonts.googleapis.com/css2?family=Fira+Sans:wght@300;400;500;600&display=swap">
<style>
  :root {
    --page-bg: #ececec;
    --label-white: #f9fafa;
    --brand-blue: #0a78c2;
    --brand-blue-light: #2a9ad8;
    --brand-blue-dark: #0563a8;
    --brand-green: #13a05a;
    --brand-teal: #1a9a8c;
    --text-grey: #6f7478;
    --hatch-grey: #e6e8ea;
  }
  * { margin: 0; padding: 0; box-sizing: border-box; }
  html, body {
    width: 1200px; height: 960px; overflow: hidden;
    background: var(--page-bg);
    font-family: "Fira Sans", Arial, sans-serif;
  }
  .label {
    position: absolute; left: 220px; top: 92px;
    width: 760px; height: 776px;
    background: var(--label-white);
    overflow: hidden;
    box-shadow: 0 6px 24px rgba(0,0,0,0.08);
  }
  .label__top-band {
    position: absolute; left: 0; top: 0; width: 100%; height: 23px;
    background: var(--brand-blue);
  }
  .label__top-stripe {
    position: absolute; left: 0; top: 23px; width: 100%; height: 8px;
    background: var(--brand-teal);
  }
  .label__tab {
    position: absolute; left: 0; top: 109px; width: 146px; height: 41px;
    background: var(--brand-green);
  }
  .brand {
    position: absolute; left: 0; top: 210px; width: 100%;
    display: flex; justify-content: center; align-items: center; gap: 18px;
  }
  .brand__dot {
    width: 44px; height: 44px; border-radius: 50%;
    background: var(--brand-teal);
  }
  .brand__name {
    font-size: 58px; font-weight: 500; letter-spacing: 6px;
    color: var(--brand-blue); text-transform: uppercase;
  }
  .title-band {
    position: absolute; left: 0; top: 339px; width: 668px; height: 175px;
    clip-path: polygon(0 0, 652px 0, 668px 16px, 668px 136px, 629px 175px, 0 175px);
  }
  .title-band__stripe {
    height: 14px;
    background: linear-gradient(90deg, var(--brand-teal), var(--brand-green) 60%, var(--brand-blue-light));
  }
  .title-band__body {
    height: 161px;
    background: linear-gradient(90deg, var(--brand-blue-light), var(--brand-blue) 45%, var(--brand-blue-dark));
    color: #fff; padding: 16px 0 0 82px; width: 100%;
  }
  .title-band__main {
    font-size: 64px; font-weight: 500; line-height: 1; width: 490px;
  }
  .title-band__sub {
    font-size: 40px; font-weight: 300; line-height: 1.2;
    width: 490px; text-align: right;
  }
  .hatch {
    position: absolute; background: var(--hatch-grey);
  }
  .hatch--under-band { left: 0; top: 514px; width: 700px; height: 30px; }
  .hatch--footer { left: 0; top: 652px; width: 100%; height: 98px; }
  .benefits {
    position: absolute; left: 187px; top: 560px; list-style: none;
  }
  .benefits li {
    font-size: 20px; font-weight: 300; color: var(--text-grey);
    line-height: 31px; display: flex; align-items: center;
  }
  .benefits li::before {
    content: ""; width: 9px; height: 9px; margin-right: 14px;
    background: var(--brand-green);
  }
  .daily {
    position: absolute; left: 0; top: 670px; width: 100%; text-align: center;
    font-size: 24px; font-weight: 600; letter-spacing: 1.5px;
    color: var(--brand-green);
  }
  .daily__rule {
    position: absolute; left: 152px; top: 706px; width: 435px; height: 4px;
    background: var(--brand-green);
  }
  .contents {
    position: absolute; left: 0; top: 719px; width: 100%; text-align: center;
    font-size: 17px; font-weight: 400; letter-spacing: 0.8px;
    color: var(--text-grey);
  }
  .label__bottom-band {
    position: absolute; left: 0; bottom: 0; width: 100%; height: 26px;
    background: var(--brand-blue);
  }
</style>
</head>
<body>
  <div class="label">
    <div class="label__top-band"></div>
    <div class="label__top-stripe"></div>
    <div class="label__tab"></div>

    <div class="brand">
      <span class="brand__dot"></span>
      <span class="brand__name">Velunor</span>
    </div>

    <div class="hatch hatch--under-band" role="img" aria-label="Light grey diagonal stripe pattern"></div>

    <div class="title-band">
      <div class="title-band__stripe"></div>
      <div class="title-band__body">
        <div class="title-band__main">Multi-Vitamin</div>
        <div class="title-band__sub">Formula</div>
      </div>
    </div>

    <ul class="benefits">
      <li>Healthy Energy Levels</li>
      <li>Healthy Immune System Function</li>
      <li>Healthy Metabolism</li>
    </ul>

    <div class="hatch hatch--footer" role="img" aria-label="Light grey diagonal stripe pattern"></div>
    <div class="daily">DAILY NUTRITION</div>
    <div class="daily__rule"></div>
    <div class="contents">60 CAPSULES &nbsp;| DIETARY SUPPLEMENT</div>

    <div class="label__bottom-band"></div>
  </div>
</body>
</html>
```